PillPeak website blog. Simple medical advice given in clear yes or no answers that save people money

I am developing a new web page that provides medical care cost savings at the consumers' fingertips. I need a web page that is clean, concise, and attractive for me to put my valuable medical information on. The information I provide is simple to obtain, yet very valuable to the consumer, and answered in a yes or no format. For example, A person may wonder if they need an antibiotic for cold like symptoms. Seeing a doctor for an antibiotic is very expensive. But with simple and clear advice at their fingertips, they can confidently avoid having to pay $200 or more to see a doctor and get an antibiotic. This is kind of like consumer reports for medical services.

Target Market(s)

People who are savvy shoppers and want to save money on healthcare. Likely younger ages between 21 and 60, who are mobile, readily use iphones, and want strong evidence based research to guide their decisions.

Industry/Entity Type

Coding

Number of Pages Required

Colors

Requirements
Must have
• A template on the "Question" and "Answer" page that can be edited many times that can be edited many times. The Confidence rating scale would need to be edited as well. The "Date Researched" the "PillPeak Pilluminate" and "References" all need to be able to be edited. This website must be very clear and simple to understand. A medical question is posed with a yes or no answer, then answered and given a confidence rating, we then tell them how much money they saved by going to our website.
Nice to have
• We want this to be slightly fun, vibrant, warm and inviting. This will be sometime later converted into an app format. Quirky, some humor to keep it interesting.
Should not have
• No sterile looking medical images. Not boring.

```html
<!DOCTYPE html>
<html lang="en">
<head>
<meta charset="utf-8">
<title>PillPeak — Clear. Valuable. Health. Advice.</title>
<link href="https://fonts.googleapis.com/css2?family=Cinzel:wght@400;700&family=Questrial&family=Poppins:wght@500;600&display=swap" rel="stylesheet">
<style>
  :root{
    --red:#dc0021;
    --red-line:#f0142f;
    --green:#169a34;
    --ink:#1a1718;
    --paper:#ebebeb;
    --footer:#231f20;
    --white:#ffffff;
    --muted:#5a5a5a;
  }
  *{box-sizing:border-box;margin:0;padding:0}
  html,body{width:1167px;height:1200px;overflow:hidden}
  body{position:relative;background:var(--paper);font-family:"Questrial",sans-serif;color:var(--ink)}
  .abs{position:absolute}

  .site-header{position:absolute;left:0;top:0;width:1167px;height:143px;background:var(--paper)}
  .brand{position:absolute;left:108px;top:36px;display:flex;align-items:center;gap:10px}
  .brand-dot{width:22px;height:22px;border-radius:50%;background:var(--red)}
  .brand-name{font-family:"Cinzel",serif;font-weight:700;font-size:32px;color:var(--red)}
  .tagline{position:absolute;right:109px;top:48px;font-family:"Cinzel",serif;font-size:32px;color:var(--red);letter-spacing:.5px;white-space:nowrap}

  .main-nav{position:absolute;left:0;top:143px;width:1167px;height:55px;background:var(--ink);display:flex;justify-content:space-between;align-items:center;padding:0 108px 0 117px}
  .main-nav a{color:#f2f2f2;text-decoration:none;font-size:15.5px}

  .search-bar{position:absolute;left:108px;top:228px;width:950px;height:43px;display:flex}
  .search-input{flex:1;border:1px solid #8a8a8a;border-right:none;background:#ececec;font-family:inherit;font-size:13px;color:var(--muted);padding-left:15px;display:flex;align-items:center}
  .search-btn{width:121px;background:var(--green);color:var(--white);font-family:"Poppins",sans-serif;font-weight:600;font-size:14px;display:flex;align-items:center;justify-content:center}

  .hero{position:absolute;left:0;top:313px;width:1167px;height:520px;background:radial-gradient(ellipse at 62% 25%,#cfe3f4 0%,#5f97cc 18%,#1f5fa6 45%,#174a86 75%,#123b6c 100%)}
  .side-menu{position:absolute;left:108px;top:402px;width:296px;background:var(--red);list-style:none}
  .side-menu li{height:50px;border-bottom:3px solid var(--red-line);display:flex;align-items:center;justify-content:space-between;padding:0 28px 0 27px;color:var(--white);font-family:"Poppins",sans-serif;font-weight:600;font-size:16.5px}
  .side-menu li:last-child{border-bottom:none}
  .side-menu svg{width:8px;height:11px}
  .hero-copy{position:absolute;right:109px;top:443px;text-align:right;color:var(--white);font-family:"Poppins",sans-serif;font-weight:600}
  .hero-copy .lead{font-size:35px;line-height:45px}
  .hero-copy .free{font-size:80px;line-height:100px;margin-top:4px}
  .slider-dots{position:absolute;left:561px;top:762px;display:flex;gap:5px}
  .slider-dots span{width:12px;height:12px;border-radius:50%;background:var(--white)}
  .slider-dots span.ring{background:transparent;border:1.5px solid var(--white)}

  .site-footer{position:absolute;left:0;top:833px;width:1167px;height:367px;background:var(--footer);color:var(--white)}
  .footer-brand{position:absolute;left:108px;top:150px;display:flex;align-items:center;gap:10px}
  .footer-brand .brand-dot{background:var(--white)}
  .footer-brand .brand-name{color:var(--white);font-size:34px}
  .footer-heading{position:absolute;top:90px;font-size:20px;font-weight:400}
  .disclaimer-text{position:absolute;left:376px;top:118px;width:300px;font-size:10px;line-height:20px;color:#e8e8e8}
  .signup{position:absolute;left:710px;top:111px;width:348px;height:44px;background:var(--white);display:flex;align-items:center;justify-content:space-between;padding:3px 2px 3px 16px}
  .signup .field{font-size:13px;color:var(--muted)}
  .signup .submit{width:116px;height:38px;background:var(--red);color:var(--white);font-family:"Poppins",sans-serif;font-weight:600;font-size:13px;display:flex;align-items:center;justify-content:center}
  .ask-box{position:absolute;left:711px;top:170px;width:347px;height:97px;background:var(--green);display:flex;align-items:center;justify-content:space-between;padding:0 22px 0 20px}
  .ask-box svg{width:78px;height:56px}
  .ask-copy{text-align:right}
  .ask-copy .title{font-family:"Poppins",sans-serif;font-weight:600;font-size:21px}
  .ask-copy .sub{font-size:16px;margin-top:2px}
  .footer-rule{position:absolute;left:108px;top:297px;width:950px;height:1px;background:#3a3536}
  .copyright{position:absolute;left:0;top:323px;width:1167px;text-align:center;font-size:13px}
</style>
</head>
<body>
  <header class="site-header">
    <div class="brand"><span class="brand-dot"></span><span class="brand-name">PillPeak</span></div>
    <p class="tagline">Clear. Valuable. Health. Advice. Right Now.</p>
  </header>

  <nav class="main-nav">
    <a href="#">Prev/Screening</a><a href="#">Women's Health</a><a href="#">Men's Health</a><a href="#">Meds</a><a href="#">Surgery</a><a href="#">Imaging</a><a href="#">Peds</a><a href="#">Contranergies</a>
  </nav>

  <div class="search-bar">
    <div class="search-input">Search entire here</div>
    <div class="search-btn">Search</div>
  </div>

  <section class="hero" role="img" aria-label="Blue abstract photo of a burst of glowing molecular strands"></section>

  <ul class="side-menu">
    <li>Who are We?<svg viewBox="0 0 8 11"><path d="M0 0L8 5.5L0 11Z" fill="#fff"/></svg></li>
    <li>How it Works<svg viewBox="0 0 8 11"><path d="M0 0L8 5.5L0 11Z" fill="#fff"/></svg></li>
    <li>How we Know<svg viewBox="0 0 8 11"><path d="M0 0L8 5.5L0 11Z" fill="#fff"/></svg></li>
    <li>Evidence based Research<svg viewBox="0 0 8 11"><path d="M0 0L8 5.5L0 11Z" fill="#fff"/></svg></li>
    <li>Dr. Whitlow<svg viewBox="0 0 8 11"><path d="M0 0L8 5.5L0 11Z" fill="#fff"/></svg></li>
    <li>Who we are not<svg viewBox="0 0 8 11"><path d="M0 0L8 5.5L0 11Z" fill="#fff"/></svg></li>
    <li>Are we Based?<svg viewBox="0 0 8 11"><path d="M0 0L8 5.5L0 11Z" fill="#fff"/></svg></li>
  </ul>

  <div class="hero-copy">
    <p class="lead">Don't Spend another time on your<br>health before checking us out!</p>
    <p class="free">It's Free!</p>
  </div>

  <div class="slider-dots"><span class="ring"></span><span></span><span></span></div>

  <footer class="site-footer">
    <div class="footer-brand"><span class="brand-dot"></span><span class="brand-name">PillPeak</span></div>

    <h3 class="footer-heading" style="left:376px">Disclaimer</h3>
    <p class="disclaimer-text">At vero eos et accusamus et iusto odio dignissimos ducimus qui blanditiis praesentium voluptatum deleniti atque corrupti quos dolores</p>

    <h3 class="footer-heading" style="left:709px">Become a PillPeak Today!</h3>
    <div class="signup"><span class="field">Enter email</span><span class="submit">SUBMIT NOW</span></div>

    <div class="ask-box">
      <svg viewBox="0 0 78 56" fill="none" stroke="#fff" stroke-width="3.5" stroke-linejoin="round">
        <path d="M46 14a20 17 0 1 1 2 30l-6 7 1-9"/>
        <path d="M28 4a24 22 0 1 0-16 38l-6 10 12-6a24 22 0 1 0 10-42z" fill="#169a34"/>
        <path d="M21 20a7 7 0 1 1 9 6c-2 1-2 3-2 5" stroke-linecap="round"/>
        <circle cx="28" cy="38" r="1.5" fill="#fff"/>
      </svg>
      <div class="ask-copy">
        <p class="title">Ask a question here!</p>
        <p class="sub">If it is worthy well Post it!</p>
      </div>
    </div>

    <div class="footer-rule"></div>
    <p class="copyright">Copyrights © 2018 PillPeak. All rights reserved.</p>
  </footer>
</body>
</html>
```